Modern Verdell Tree Care Website

I need a website for a full service Tree Care company. The company provides tree pruning, tree removal, tree preservation, emergency services, stump grinding, and emergency tree services.

Target Market(s)

Customers that need tree services

Industry/Entity Type

Landscaping, Tree Services

Coding

Coded - Design and coding required

Number of Pages Required

5+ page

Font styles to use
Sans Serif

Requirements
Must have
• Good clean design that showcases the services the company provides.
Nice to have
• Services page; contact form, blog, home page, about page

```html
<!DOCTYPE html>
<html lang="en">
<head>
<meta charset="utf-8">
<title>Verdell Tree Care</title>
<link rel="stylesheet" href="https://fonts.googleapis.com/css2?family=Montserrat:wght@300;400;500;600;700;800&family=Open+Sans:wght@400;600&display=swap">
<style>
:root{
  --green:#7dbb3a;
  --green-dark:#3f6a1e;
  --orange:#f7a830;
  --ink:#1f2420;
  --text:#3a3d3a;
  --cream:#f1f0e8;
  --white:#fff;
  --line:#d9d9d2;
}
*{box-sizing:border-box;margin:0;padding:0}
html,body{width:1200px;height:4789px;overflow:hidden}
body{position:relative;background:var(--white);font-family:"Open Sans",sans-serif;color:var(--text)}
.abs{position:absolute}
h1,h2,h3,h4{font-family:"Montserrat",sans-serif}
.light{color:var(--green);font-weight:300}
.btn{position:absolute;display:flex;align-items:center;justify-content:center;font-family:"Montserrat",sans-serif;font-weight:700;color:#fff;text-transform:uppercase}
.photo{position:absolute}
.brand{display:flex;align-items:center;gap:10px;font-family:"Montserrat",sans-serif;font-weight:800;color:var(--ink);letter-spacing:.5px;white-space:nowrap}
.brand .mark{width:36px;height:36px;background:var(--green);flex:none}
.sec-mark{width:28px;height:28px;background:var(--orange);margin:0 auto}
.uline{width:70px;height:3px;background:var(--orange)}

/* header */
.site-header{position:absolute;left:0;top:0;width:1200px;height:80px;z-index:5}
.site-header .brand{position:absolute;left:85px;top:24px;font-size:15px}
.nav{position:absolute;left:337px;top:35px;display:flex;font-family:"Montserrat",sans-serif;font-size:13px;font-weight:500;color:var(--ink)}
.nav a{text-decoration:none;color:inherit;margin-right:42px;position:relative}
.nav a.active{color:var(--green)}
.nav a.active::after{content:"";position:absolute;left:0;right:0;bottom:-8px;height:2px;background:var(--green)}
.phone-btn{left:945px;top:20px;width:176px;height:44px;border-radius:22px;background:var(--green);font-size:14px;font-weight:600;text-transform:none;gap:8px}
.phone-ico{width:24px;height:24px;border-radius:50%;background:#fff;display:flex;align-items:center;justify-content:center}

/* hero */
.hero{position:absolute;left:0;top:0;width:1200px;height:678px;background:#fff}
.hero-photo{left:0;top:0;width:1200px;height:678px;background:linear-gradient(90deg,#ffffff 0%,#f3f7fa 38%,#c9dced 55%,#7fa14a 72%,#5d8a34 85%,#a9c7e2 100%)}
.hero-copy{position:absolute;left:115px;top:232px}
.hero-copy .eyebrow{font-family:"Montserrat",sans-serif;font-size:16px;font-weight:500;color:var(--ink);letter-spacing:.5px}
.hero-copy h1{font-size:39px;line-height:46px;font-weight:700;color:var(--ink);margin-top:8px}
.hero-copy h1 span{color:var(--green)}
.hero-copy p{font-size:17px;margin-top:10px;color:var(--text)}
.hero-btn{left:115px;top:400px;width:150px;height:42px;background:var(--orange);font-size:13px;border-radius:2px}

/* about */
.about{position:absolute;left:0;top:730px;width:1200px;height:520px}
.about-photo{left:152px;top:80px;width:374px;height:372px;background:linear-gradient(160deg,#5f8d34,#a9c98a 45%,#e8892c 60%,#4c6f2a)}
.about-copy{position:absolute;left:610px;top:50px;width:515px}
.about-copy h2{font-size:36px;line-height:42px;font-weight:700;color:var(--ink)}
.about-copy p{font-size:14.5px;line-height:23px;margin-top:26px}
.about-copy blockquote{border-left:2px solid var(--orange);padding-left:18px;margin-top:22px;font-size:14.5px;line-height:23px;margin-left:4px}
.about-btn{left:615px;top:388px;width:193px;height:56px;border-radius:28px;background:var(--green);font-size:16px;font-weight:600}

/* services */
.services{position:absolute;left:0;top:1298px;width:1200px;height:690px;background:var(--cream)}
.services .sec-mark{position:absolute;left:586px;top:42px}
.sec-title{position:absolute;left:0;width:1200px;text-align:center;font-size:34px;font-weight:700;color:var(--ink)}
.services .uline{position:absolute;left:565px;top:124px}
.card{position:absolute;width:302px;height:215px;border-radius:28px 0 28px 0;overflow:hidden}
.card .label{position:absolute;left:0;right:0;bottom:28px;text-align:center;font-family:"Montserrat",sans-serif;font-size:17px;font-weight:700;color:#fff;letter-spacing:.3px}
.card .label::after{content:"";display:block;width:36px;height:2px;background:#fff;margin:8px auto 0}
.card.active{background:linear-gradient(160deg,#4d7a34,#2d5424)}
.card.active h4{position:absolute;top:40px;width:100%;text-align:center;color:#fff;font-size:17px;font-weight:700}
.card.active p{position:absolute;top:76px;left:38px;right:38px;text-align:center;color:#fff;font-size:11px;line-height:17px}
.card.active .mini{position:absolute;left:92px;top:140px;width:112px;height:26px;border-radius:13px;background:var(--green);color:#fff;font-family:"Montserrat",sans-serif;font-size:8.5px;font-weight:700;display:flex;align-items:center;justify-content:center}

/* why */
.why{position:absolute;left:0;top:1988px;width:1200px;height:737px}
.why .sec-mark{position:absolute;left:596px;top:78px}
.why .uline{position:absolute;left:575px;top:158px}
.tree{left:435px;top:202px;width:325px;height:290px;background:linear-gradient(180deg,#eef5e6 0%,#9cc46a 30%,#5f9634 65%,#e9efe1 100%)}
.feat{position:absolute;width:76px;height:76px;border-radius:50%;display:flex;align-items:center;justify-content:center}
.feat.g{background:var(--green)}
.feat.o{background:var(--orange)}
.feat-label{position:absolute;font-family:"Montserrat",sans-serif;font-size:14.5px;font-weight:700;line-height:19px;color:var(--ink)}
.feat-label.r{text-align:right}

/* blogs */
.blogs{position:absolute;left:0;top:2725px;width:1200px;height:641px;background:var(--cream)}
.blogs h2{position:absolute;left:103px;top:52px;font-size:36px;font-weight:700;color:var(--ink);display:flex;align-items:center;gap:10px}
.blogs h2 .sq{width:28px;height:28px;background:var(--orange)}
.blogs .uline{position:absolute;left:103px;top:105px}
.post-lg{position:absolute;left:106px;top:143px;width:473px;height:407px;background:#fff;border:1px solid var(--line)}
.post-lg .img{left:0;top:0;width:471px;height:285px;background:linear-gradient(120deg,#3d5a2e,#8c9a86 45%,#6e5e4c 75%,#4b4034)}
.date{position:absolute;background:var(--green);color:#fff;font-family:"Montserrat",sans-serif;font-weight:600}
.post-lg .date{left:0;top:254px;width:140px;height:32px;font-size:13px;display:flex;align-items:center;justify-content:center}
.post-lg h3{position:absolute;left:40px;top:310px;width:400px;font-size:18px;line-height:27px;font-weight:600;color:var(--ink)}
.more{font-family:"Montserrat",sans-serif;font-weight:600;color:var(--green);text-decoration:underline;font-size:13px}
.post-lg .more{position:absolute;left:40px;top:370px}
.post-sm{position:absolute;left:600px;width:501px;height:194px;background:#fff;border:1px solid var(--line)}
.post-sm .img{left:0;top:0;width:236px;height:192px}
.post-sm .date{left:262px;top:45px;width:80px;height:20px;font-size:9.5px;display:flex;align-items:center;justify-content:center}
.post-sm h3{position:absolute;left:262px;top:78px;width:215px;font-size:14.5px;line-height:19px;font-weight:600;color:var(--ink)}
.post-sm .more{position:absolute;left:262px;top:144px;font-size:11px}

/* reviews */
.reviews{position:absolute;left:0;top:3366px;width:1200px;height:513px;background:#fff;overflow:hidden}
.reviews-bg{left:0;top:0;width:545px;height:513px}
.reviews-copy{position:absolute;left:112px;top:140px;color:#fff}
.reviews-copy h2{font-size:27px;line-height:36px;font-weight:700}
.reviews-copy .tag{font-family:"Montserrat",sans-serif;font-size:17px;font-weight:700;margin-top:22px}
.stars{letter-spacing:3px}
.reviews-copy .stars{font-size:28px;line-height:32px}
.reviews-copy .meta{font-size:13px;margin-top:4px}
.bubble{position:absolute;width:310px;height:310px;border-radius:50%;background:#fff;border:3px solid var(--green);box-shadow:0 0 0 10px #f4f6ef;text-align:center}
.bubble .q{font-family:"Montserrat",sans-serif;font-size:54px;font-weight:800;color:var(--orange);line-height:40px;margin-top:40px}
.bubble p{font-size:12.5px;line-height:23px;margin:12px 34px 0}
.bubble h4{font-size:15px;font-weight:700;color:var(--ink);margin-top:6px}
.bubble .stars{color:var(--orange);font-size:20px}
.arrow{position:absolute;top:238px}

/* contact */
.contact{position:absolute;left:0;top:3879px;width:1200px;height:579px;background:linear-gradient(180deg,#eceae0,#f4f3ec);overflow:hidden}
.contact-shape{left:0;top:0;width:1200px;height:579px}
.contact h2{position:absolute;left:112px;top:70px;font-size:36px;font-weight:700;color:var(--ink);display:flex;align-items:center;gap:12px}
.contact h2 .sq{width:28px;height:28px;background:var(--orange)}
.field{position:absolute;left:115px;width:415px;height:44px;background:#fff;border:1px solid var(--line);font-size:12.5px;color:#555;padding:14px 22px}
.send-btn{left:115px;top:430px;width:168px;height:42px;border-radius:21px;background:var(--green);font-size:12.5px}
.contact-ring{left:605px;top:55px;width:480px;height:480px;border-radius:50%;border:10px solid var(--green-dark)}
.contact-photo{left:630px;top:80px;width:430px;height:430px;border-radius:50%;background:linear-gradient(160deg,#8fbf55 0%,#5f9634 45%,#3f6a24 100%)}

/* footer */
.site-footer{position:absolute;left:0;top:4458px;width:1200px;height:331px;background:#fff}
.site-footer .brand{position:absolute;left:0;width:1200px;justify-content:center;top:44px;font-size:28px}
.site-footer .brand .mark{width:46px;height:46px}
.rule{position:absolute;left:103px;width:995px;height:1px;background:var(--line)}
.foot-nav{position:absolute;left:0;width:1200px;top:152px;display:flex;justify-content:center;font-family:"Montserrat",sans-serif;font-size:14px;font-weight:600;color:var(--ink)}
.foot-nav span.dot{color:var(--green);margin:0 42px}
.foot-contact{position:absolute;top:222px;display:flex;align-items:center;gap:10px;font-size:13.5px;font-weight:600;color:var(--ink)}
.ci{width:34px;height:34px;border-radius:50%;background:var(--green);display:flex;align-items:center;justify-content:center}
.socials{position:absolute;left:926px;top:228px;display:flex;gap:14px}
.socials span{width:26px;height:26px;border-radius:50%;background:var(--green-dark)}
.copyright{position:absolute;left:0;top:283px;width:1200px;height:48px;background:var(--cream);display:flex;align-items:center;justify-content:center;font-size:12.5px;color:#444}
</style>
</head>
<body>

<section class="hero">
  <div class="photo hero-photo" role="img" aria-label="Arborist in harness climbing among green tree branches against a blue sky"></div>
  <div class="hero-copy">
    <div class="eyebrow">WELCOME TO VERDELL TREE CARE</div>
    <h1>VERDELL FOR ALL YOUR<br><span>TREE CARE NEEDS</span></h1>
    <p>Serving Maplewood and surrounding areas.</p>
  </div>
  <a class="btn hero-btn">Contact Us</a>
</section>

<header class="site-header">
  <div class="brand"><span class="mark"></span>VERDELL TREE CARE</div>
  <nav class="nav">
    <a class="active">HOME</a><a>ABOUT US</a><a>SERVICES</a><a>BLOG</a><a>REVIEW</a><a>CONTACT US</a>
  </nav>
  <a class="btn phone-btn"><span class="phone-ico"><svg width="14" height="14" viewBox="0 0 24 24"><path fill="#7dbb3a" d="M6.6 10.8a15.1 15.1 0 0 0 6.6 6.6l2.2-2.2c.3-.3.7-.4 1-.2 1.1.4 2.3.6 3.6.6.6 0 1 .4 1 1V20c0 .6-.4 1-1 1A17 17 0 0 1 3 4c0-.6.4-1 1-1h3.5c.6 0 1 .4 1 1 0 1.3.2 2.5.6 3.6.1.3 0 .7-.2 1z"/></svg></span>(555) 214-7380</a>
</header>

<section class="about">
  <svg class="abs" style="left:0;top:0" width="430" height="520"><polygon points="0,0 420,0 195,520 0,520" fill="#7dbb3a"/></svg>
  <div class="photo about-photo" role="img" aria-label="Arborist in orange shirt and helmet working in a tree"></div>
  <div class="about-copy">
    <h2>ABOUT VERDELL<br><span class="light">TREE CARE</span></h2>
    <p>At Verdell Tree Care, we are more than just a tree service company, we are stewards of our beautiful trees. With a passion deeply rooted in arboriculture, we embark on a mission to promote the health, beauty, and safety of your trees and landscapes.</p>
    <blockquote>Whether it's expert tree trimming to enhance aesthetics, meticulous tree removal to mitigate hazards, or comprehensive tree health assessments to ensure safety, we approach each task with unwavering dedication and attention to detail.</blockquote>
  </div>
  <a class="btn about-btn">Learn More</a>
</section>

<section class="services">
  <div class="sec-mark"></div>
  <h2 class="sec-title" style="top:76px">SERVICES <span class="light">PROVIDE</span></h2>
  <div class="uline"></div>
  <div class="card" style="left:118px;top:162px;background:linear-gradient(150deg,#8aa06a,#5f7444 50%,#3d4f2b)" role="img" aria-label="Pruning shears cutting a branch"><div class="label">TREE PRUNING</div></div>
  <div class="card active" style="left:445px;top:162px">
    <h4>TREE REMOVAL</h4>
    <p>Lorem ipsum dolor sit amet, consectetur adipiscing elit, sed do eiusmod tempor incididunt ut labore et dolore</p>
    <div class="mini">LEARN MORE</div>
  </div>
  <div class="card" style="left:772px;top:162px;background:linear-gradient(160deg,#9bc45a,#6e9a3a 45%,#5a3a24)" role="img" aria-label="Young tree being planted in soil"><div class="label">TREE PRESERVATION</div></div>
  <div class="card" style="left:118px;top:402px;background:linear-gradient(160deg,#5e8a3a,#8a6a46 50%,#4d3a26)" role="img" aria-label="Large tree stump being ground"><div class="label">STUMP GRINDING</div></div>
  <div class="card" style="left:445px;top:402px;background:linear-gradient(160deg,#6e8c4a,#4f6a36 50%,#3a4d2a)" role="img" aria-label="Fallen tree across a yard after a storm"><div class="label">TREE EMERGENCY SERVICES</div></div>
  <div class="card" style="left:772px;top:402px;background:linear-gradient(160deg,#4e7a3a,#8a7a5a 45%,#d2782e 60%,#3d5a2a)" role="img" aria-label="Arborist installing cables high in a tree"><div class="label">CABLING &amp; BRACING</div></div>
</section>

<section class="why">
  <div class="sec-mark"></div>
  <h2 class="sec-title" style="top:112px">WHY CHOOSE <span class="light">VERDELL</span></h2>
  <div class="uline"></div>
  <svg class="abs" style="left:0;top:0" width="1200" height="737"><path d="M356 380 A255 255 0 0 0 834 380" fill="none" stroke="#f7a830" stroke-width="1.5"/><path d="M381 234 A255 255 0 0 0 356 380" fill="none" stroke="#f7a830" stroke-width="1.5"/><path d="M834 380 A255 255 0 0 0 810 241" fill="none" stroke="#f7a830" stroke-width="1.5"/></svg>
  <div class="photo tree" role="img" aria-label="Large healthy green tree"></div>

  <div class="feat g" style="left:343px;top:196px"><svg width="34" height="34" viewBox="0 0 24 24" fill="none" stroke="#fff" stroke-width="1.5"><rect x="5" y="3" width="14" height="18" rx="1"/><path d="M9 12l2 2 4-4"/></svg></div>
  <div class="feat-label r" style="left:180px;top:212px;width:141px">LICENSED AND<br>INSURED</div>

  <div class="feat o" style="left:319px;top:342px"><svg width="34" height="34" viewBox="0 0 24 24" fill="none" stroke="#fff" stroke-width="1.5"><circle cx="12" cy="12" r="9"/><path d="M12 7v5l3 2"/></svg></div>
  <div class="feat-label r" style="left:110px;top:368px;width:198px">24 HOUR EMERGENCY<br>SERVICES</div>

  <div class="feat g" style="left:382px;top:482px"><svg width="34" height="34" viewBox="0 0 24 24" fill="none" stroke="#fff" stroke-width="1.5"><path d="M12 21s-6-6.5-6-11a6 6 0 0 1 12 0c0 4.5-6 11-6 11z"/><circle cx="12" cy="10" r="2"/></svg></div>
  <div class="feat-label r" style="left:200px;top:511px;width:170px">LOCALLY OWNED<br>&amp; OPERATED</div>

  <div class="feat o" style="left:551px;top:556px"><svg width="34" height="34" viewBox="0 0 24 24" fill="none" stroke="#fff" stroke-width="1.5"><circle cx="12" cy="8" r="3"/><path d="M6 20c0-3.3 2.7-6 6-6s6 2.7 6 6"/></svg></div>
  <div class="feat-label" style="left:490px;top:643px;width:200px;text-align:center">LICENSED ARBORIST<br>ON STAFF</div>

  <div class="feat g" style="left:744px;top:491px"><svg width="34" height="34" viewBox="0 0 24 24" fill="none" stroke="#fff" stroke-width="1.5"><rect x="4" y="4" width="16" height="16" rx="1"/><path d="M8 9h8M8 13h8M8 17h5"/></svg></div>
  <div class="feat-label" style="left:831px;top:521px;width:180px">FREE ESTIMATE</div>

  <div class="feat o" style="left:796px;top:344px"><svg width="34" height="34" viewBox="0 0 24 24" fill="none" stroke="#fff" stroke-width="1.5"><path d="M12 3l7 3v6c0 4-3 7-7 9-4-2-7-5-7-9V6z"/><path d="M9 12l2 2 4-4"/></svg></div>
  <div class="feat-label" style="left:886px;top:362px;width:150px">SAFETY IS OUR<br>TOP PRIORITY</div>

  <div class="feat g" style="left:772px;top:203px"><svg width="34" height="34" viewBox="0 0 24 24" fill="none" stroke="#fff" stroke-width="1.5"><circle cx="12" cy="9" r="6"/><path d="M12 15v6M9 21h6"/></svg></div>
  <div class="feat-label" style="left:862px;top:220px;width:150px">PROFESSIONAL<br>WORK</div>
</section>

<section class="blogs">
  <h2>LATEST <span class="light">BLOGS</span><span class="sq"></span></h2>
  <div class="uline"></div>
  <article class="post-lg">
    <div class="photo img" role="img" aria-label="Chainsaw cutting into a large tree trunk"></div>
    <div class="date">20 MAY 2024</div>
    <h3>Lorem ipsum dolor sit amet consectetur adipiscing elit sed do eiusmod</h3>
    <a class="more">LEARN MORE</a>
  </article>
  <article class="post-sm" style="top:143px">
    <div class="photo img" style="background:linear-gradient(150deg,#7aa84a,#4e6a34 45%,#c8c0a8 60%,#5e7a3a)" role="img" aria-label="Climber in harness on a tree trunk"></div>
    <div class="date">20 MAY 2024</div>
    <h3>Lorem ipsum dolor sit amet consectetur adipiscing elit sed do eiusmod</h3>
    <a class="more">LEARN MORE</a>
  </article>
  <article class="post-sm" style="top:355px">
    <div class="photo img" style="background:linear-gradient(150deg,#8ab85a,#a9c48a 45%,#c23a2a 55%,#6e9a3e)" role="img" aria-label="Gardener trimming branches with long pruners"></div>
    <div class="date">10 MAY 2024</div>
    <h3>Lorem ipsum dolor sit amet consectetur adipiscing elit sed do eiusmod</h3>
    <a class="more">LEARN MORE</a>
  </article>
</section>

<section class="reviews">
  <svg class="abs reviews-bg" width="545" height="513"><polygon points="0,0 540,0 318,513 0,513" fill="#f7a830"/></svg>
  <div class="reviews-copy">
    <h2>WHAT PEOPLE<br>ARE SAYING<br>ABOUT US</h2>
    <div class="tag">EXLLENT SERVICE</div>
    <div class="stars">★★★★★</div>
    <div class="meta">4.8 Rating &nbsp;|&nbsp; 3500 Reviews</div>
  </div>
  <svg class="arrow" style="left:374px" width="14" height="24"><path d="M12 2L3 12l9 10" fill="none" stroke="#7dbb3a" stroke-width="2"/></svg>
  <div class="bubble" style="left:413px;top:75px">
    <div class="q">“</div>
    <p>“Lorem ipsum dolor sit amet, consectetur adipiscing elit, sed do eiusmod tempor incididunt ut labore et dolore magna aliqua Quis ipsum suspendisse ultrices gravida Risus commodo viverra maecenas ”</p>
    <h4>Daniel Hartley</h4>
    <div class="stars">★★★★★</div>
  </div>
  <div class="bubble" style="left:757px;top:75px">
    <div class="q">“</div>
    <p>“Lorem ipsum dolor sit amet, consectetur adipiscing elit, sed do eiusmod tempor incididunt ut labore et dolore magna aliqua Quis ipsum suspendisse ultrices gravida Risus commodo viverra maecenas ”</p>
    <h4>Daniel Hartley</h4>
    <div class="stars">★★★★★</div>
  </div>
  <div class="bubble" style="left:1120px;top:75px;border-color:#e6e6e0"></div>
  <svg class="arrow" style="left:1090px" width="14" height="24"><path d="M2 2l9 10-9 10" fill="none" stroke="#7dbb3a" stroke-width="2"/></svg>
</section>

<section class="contact">
  <svg class="abs contact-shape" width="1200" height="579"><polygon points="1010,0 1200,0 1200,579 710,579" fill="#7dbb3a"/></svg>
  <h2>CONTACT <span class="light">US</span><span class="sq"></span></h2>
  <div class="field" style="top:162px">First Name*</div>
  <div class="field" style="top:217px">Email address</div>
  <div class="field" style="top:272px">Phone number</div>
  <div class="field" style="top:325px;height:86px">Leave Message</div>
  <a class="btn send-btn">Send Message</a>
  <div class="abs contact-ring"></div>
  <svg class="abs" style="left:605px;top:55px" width="480" height="480"><path d="M80 400 A235 235 0 0 0 400 400" fill="none" stroke="#f7a830" stroke-width="10"/></svg>
  <div class="photo contact-photo" role="img" aria-label="Arborist in orange shirt and helmet roped into a leafy tree"></div>
</section>

<footer class="site-footer">
  <div class="brand"><span class="mark"></span>VERDELL TREE CARE</div>
  <div class="rule" style="top:130px"></div>
  <div class="foot-nav">HOME<span class="dot">•</span>ABOUT US<span class="dot">•</span>SERVICES<span class="dot">•</span>BLOGS<span class="dot">•</span>REVIEWS<span class="dot">•</span>CONTACT</div>
  <div class="rule" style="top:185px"></div>
  <div class="foot-contact" style="left:198px"><span class="ci"><svg width="16" height="16" viewBox="0 0 24 24"><path fill="#fff" d="M6.6 10.8a15.1 15.1 0 0 0 6.6 6.6l2.2-2.2c.3-.3.7-.4 1-.2 1.1.4 2.3.6 3.6.6.6 0 1 .4 1 1V20c0 .6-.4 1-1 1A17 17 0 0 1 3 4c0-.6.4-1 1-1h3.5c.6 0 1 .4 1 1 0 1.3.2 2.5.6 3.6.1.3 0 .7-.2 1z"/></svg></span>(555) 214-7380</div>
  <div class="foot-contact" style="left:432px"><span class="ci"><svg width="16" height="16" viewBox="0 0 24 24"><path fill="#fff" d="M6.6 10.8a15.1 15.1 0 0 0 6.6 6.6l2.2-2.2c.3-.3.7-.4 1-.2 1.1.4 2.3.6 3.6.6.6 0 1 .4 1 1V20c0 .6-.4 1-1 1A17 17 0 0 1 3 4c0-.6.4-1 1-1h3.5c.6 0 1 .4 1 1 0 1.3.2 2.5.6 3.6.1.3 0 .7-.2 1z"/></svg></span>(555) 309-6621</div>
  <div class="foot-contact" style="left:634px;font-size:12.5px"><span class="ci"><svg width="16" height="16" viewBox="0 0 24 24" fill="none" stroke="#fff" stroke-width="2"><rect x="3" y="5" width="18" height="14" rx="1"/><path d="M3 6l9 7 9-7"/></svg></span>hello@verdelltreecare.com</div>
  <div class="socials"><span></span><span></span><span></span><span></span></div>
  <div class="copyright">Copyright © 2024 Verdell Tree Care | &nbsp;All Right Reserved</div>
</footer>

</body>
</html>
```